Business Card Design

We custom build & and install Air filtration systems for mining machines - the system filters the air going into the cabin to protect the operator/driver Examples of the machines we install our units to would be Ironhaven or Veltoro. Australian owned company Our company colors are sky blue with polished Stainless steel lettering & framing. I have a logo which I will upload but I would like the new image to be crisper.

Industry/Entity Type

Business

Contact Information for Business Card

Company name - Clearlung Pty Ltd
Dale Morrissey - Position - Sales & Product Development Contact numbers Mob 0428 359 162 Tel - 07 3581 4296
Address - 147 Quarrel Rd, Wendlebury, Brisbane 4108, Australia

Colors
0255a3

Requirements
Must have
• sky blue & polished chrome lettering

```html
<!DOCTYPE html>
<html lang="en">
<head>
<meta charset="utf-8">
<title>Clearlung Business Card</title>
<link rel="stylesheet" href="https://fonts.googleapis.com/css2?family=Exo+2:wght@500;600;700&display=swap">
<style>
  :root {
    --page-bg: #e4e6ea;
    --card-bg: #fbfbfc;
    --sky-blue: #1f8fd8;
    --chrome: #7d8790;
    --ink: #3a3d42;
    --avatar-grey: #8a9098;
    --icon-white: #ffffff;
  }
  * { margin: 0; padding: 0; box-sizing: border-box; }
  html, body {
    width: 1200px;
    height: 816px;
    overflow: hidden;
    background: var(--page-bg);
    font-family: "Exo 2", sans-serif;
    color: var(--ink);
  }
  .card {
    position: absolute;
    left: 100px;
    top: 122px;
    width: 1000px;
    height: 572px;
    background: var(--card-bg);
    border-radius: 44px;
    border: 2px solid #d3d8dd;
    box-shadow: 0 10px 30px rgba(0, 0, 0, 0.12);
  }
  .rule {
    position: absolute;
    height: 4px;
    background: var(--sky-blue);
  }
  .rule--top { left: 150px; top: 150px; width: 330px; }
  .rule--bottom { left: 70px; top: 258px; width: 410px; }

  .identity {
    position: absolute;
    left: 78px;
    top: 178px;
    display: flex;
    align-items: center;
    gap: 18px;
  }
  .identity__avatar { width: 44px; height: 44px; flex: none; }
  .identity__name {
    font-size: 23px;
    font-weight: 600;
    letter-spacing: 1.5px;
    text-transform: uppercase;
    line-height: 1.1;
    color: var(--chrome);
  }
  .identity__role {
    font-size: 19px;
    font-weight: 500;
    letter-spacing: 1.2px;
    line-height: 1.25;
  }

  .contacts {
    position: absolute;
    left: 78px;
    top: 300px;
    list-style: none;
  }
  .contact {
    display: flex;
    align-items: center;
    gap: 18px;
    height: 58px;
    margin-bottom: 14px;
  }
  .contact__icon { width: 44px; height: 44px; flex: none; }
  .contact__text {
    font-size: 19px;
    font-weight: 500;
    letter-spacing: 1.3px;
    line-height: 1.3;
  }

  .brand {
    position: absolute;
    left: 580px;
    top: 238px;
    display: flex;
    align-items: center;
    gap: 18px;
  }
  .brand__mark {
    width: 46px;
    height: 46px;
    background: var(--sky-blue);
  }
  .brand__name {
    font-size: 64px;
    font-weight: 700;
    color: var(--chrome);
    letter-spacing: 1px;
    line-height: 1;
  }
</style>
</head>
<body>
  <main class="card">
    <div class="rule rule--top"></div>

    <div class="identity">
      <svg class="identity__avatar" viewBox="0 0 44 44" aria-hidden="true">
        <circle cx="22" cy="22" r="22" fill="var(--avatar-grey)"/>
        <circle cx="22" cy="17" r="7" fill="var(--icon-white)"/>
        <path d="M10 34c1.5-7 6.5-10 12-10s10.5 3 12 10z" fill="var(--icon-white)"/>
      </svg>
      <div>
        <p class="identity__name">Dale Morrissey</p>
        <p class="identity__role">Sales &amp; Product Development</p>
      </div>
    </div>

    <div class="rule rule--bottom"></div>

    <ul class="contacts">
      <li class="contact">
        <svg class="contact__icon" viewBox="0 0 44 44" aria-hidden="true">
          <circle cx="22" cy="22" r="22" fill="var(--sky-blue)"/>
          <rect x="16" y="11" width="12" height="22" rx="2" fill="none" stroke="var(--icon-white)" stroke-width="2"/>
          <circle cx="22" cy="29" r="1.3" fill="var(--icon-white)"/>
        </svg>
        <p class="contact__text">Mob 0428 359 162<br>Tel 07 3581 4296</p>
      </li>
      <li class="contact">
        <svg class="contact__icon" viewBox="0 0 44 44" aria-hidden="true">
          <circle cx="22" cy="22" r="22" fill="var(--sky-blue)"/>
          <rect x="11" y="13" width="22" height="14" rx="1.5" fill="none" stroke="var(--icon-white)" stroke-width="2"/>
          <path d="M18 32h8M22 27v5" stroke="var(--icon-white)" stroke-width="2"/>
        </svg>
        <p class="contact__text">sales@clearlung.au<br>clearlung.au</p>
      </li>
      <li class="contact">
        <svg class="contact__icon" viewBox="0 0 44 44" aria-hidden="true">
          <circle cx="22" cy="22" r="22" fill="var(--sky-blue)"/>
          <path d="M22 34s-8-8.5-8-14a8 8 0 0 1 16 0c0 5.5-8 14-8 14z" fill="var(--icon-white)"/>
          <circle cx="22" cy="20" r="3" fill="var(--sky-blue)"/>
        </svg>
        <p class="contact__text">147 Quarrel Rd, Wendlebury<br>Brisbane QLD 4108</p>
      </li>
    </ul>

    <div class="brand">
      <span class="brand__mark" aria-hidden="true"></span>
      <span class="brand__name">Clearlung</span>
    </div>
  </main>
</body>
</html>
```